Letter design, envelope design, and more

Hello, we the Tavrin Gmbh are looking for our shop. Letter C5. Design does not have to be like a business card, so it can have straight lines. Only the color is important. The logo is the text under TaVRin omit.It should not be playful but Profesionel

Font styles to use
Sans Serif

Colors
0555a3
3176b5
85abd2
85cae6
34a7d8
0792cd
cee9f5
cfdfed
000000

Requirements
Must have
• Color like business card, Please, with the text under TaVRin, Correct address Lindmattstr. 4 Zip code 9517 Seewil, as well as Couvert Without addressing only design and logo with TaVrn
Nice to have
• more writing articles
Should not have
• Not too colored, Text under TaVRin, bright colors

```html
<!DOCTYPE html>
<html lang="en">
<head>
<meta charset="utf-8">
<title>Tavrin Gmbh – Letterhead and Envelope</title>
<link rel="stylesheet" href="https://fonts.googleapis.com/css2?family=Source+Sans+3:wght@400;600&family=Arimo:wght@700&display=swap">
<style>
  :root {
    --navy: #1d3a78;
    --brand-blue: #0555a3;
    --mid-blue: #3176b5;
    --flap-blue: #85abd2;
    --ink: #000000;
    --body-ink: #2a2a2a;
    --paper: #ffffff;
    --backdrop: #e2e2e2;
  }
  * { margin: 0; padding: 0; box-sizing: border-box; }
  html, body { width: 1200px; height: 800px; overflow: hidden; }
  body { background: var(--backdrop); position: relative; font-family: "Source Sans 3", sans-serif; }

  .brand { display: flex; align-items: center; gap: 8px; position: absolute; }
  .brand-square { width: 26px; height: 30px; background: var(--navy); }
  .brand-name { font-family: "Source Sans 3", sans-serif; font-weight: 600; font-size: 24px; color: var(--navy); letter-spacing: 0.5px; line-height: 1; }

  .letter { position: absolute; left: 81px; top: 58px; width: 482px; height: 683px; background: var(--paper); }
  .letter .brand { left: 37px; top: 33px; }
  .contact { position: absolute; left: 351px; top: 37px; font-size: 8px; line-height: 10px; color: var(--ink); }
  .contact li { list-style: none; display: flex; align-items: center; gap: 3px; }
  .contact svg { width: 7px; height: 6px; }
  .salutation { position: absolute; left: 37px; top: 139px; font-family: "Arimo", sans-serif; font-weight: 700; font-size: 11.5px; color: var(--ink); }
  .letter-body { position: absolute; left: 37px; top: 166px; width: 409px; font-size: 10.2px; line-height: 12.8px; color: var(--body-ink); text-align: justify; }
  .letter-body p + p { margin-top: 12.4px; }
  .signature { position: absolute; left: 42px; top: 450px; width: 82px; height: 40px; background: linear-gradient(90deg, #e9e9e9, #f4f4f4); border-radius: 20px; }

  .footer-band { position: absolute; left: 0; bottom: 0; width: 100%; height: 16px; }
  .footer-url { position: absolute; right: 34px; bottom: 2px; font-size: 8px; letter-spacing: 1.6px; color: var(--paper); }

  .envelope { position: absolute; left: 594px; top: 364px; width: 526px; height: 371px; background: var(--paper); }
  .envelope-flap { position: absolute; left: 594px; top: 294px; width: 526px; height: 71px; }
  .envelope .brand { left: 28px; top: 22px; }
</style>
</head>
<body>

<section class="letter" aria-label="Letterhead">
  <div class="brand"><span class="brand-square"></span><span class="brand-name">TaVRin</span></div>
  <ul class="contact">
    <li><svg viewBox="0 0 7 6"><path d="M0.5 2 Q3.5 -0.5 6.5 2 L5.5 3 L4.6 2.2 L2.4 2.2 L1.5 3 Z M1.5 3.5 H5.5 V5.5 H1.5 Z" fill="var(--mid-blue)"/></svg>+41 71 555 40 20</li>
    <li><svg viewBox="0 0 7 6"><path d="M0.5 1 H6.5 V5 H0.5 Z" fill="var(--mid-blue)"/><path d="M0.5 1 L3.5 3.4 L6.5 1" stroke="#fff" stroke-width="0.7" fill="none"/></svg>info@tavrin.ch</li>
    <li>Lindmattstr. 4&nbsp; 9517 Seewil,</li>
  </ul>

  <p class="salutation">Dear Mr. Berger,</p>

  <div class="letter-body">
    <p>Lorem Ipsum is simply dummy text of the printing and typesetting industry. Lorem Ipsum has been the industry's standard dummy text ever since the 1500s, when an unknown printer took a galley of type and scrambled it to make a type specimen book. It has survived not only five centuries, but also the leap into electronic typesetting, remaining essentially unchanged.</p>
    <p>The standard chunk of Lorem Ipsum used since the 1500s is reproduced below for those interested. Sections 1.10.32 and 1.10.33 from "de Finibus Bonorum et Malorum" by Corvan are also reproduced in their exact original form, accompanied by English versions from the 1914 translation by H. Rowland</p>
    <p>Lorem Ipsum is simply dummy text of the printing and typesetting industry. Lorem Ipsum has been the industry's standard dummy text ever since the 1500s, when an unknown printer took a galley of type and scrambled it to make a type specimen book. It has survived not only five centuries, but also the leap into electronic typesetting, remaining essentially unchanged. It was popularised in the</p>
    <p>The standard chunk of Lorem Ipsum used since the 1500s is reproduced below for those interested. Sections 1.10.32 and 1.10.33 from "de Finibus Bonorum et Malorum" by Corvan are also reproduced in their exact original form, accompanied by English versions from the 1914 translation by H. Rowland</p>
  </div>

  <div class="signature" role="img" aria-label="Handwritten signature"></div>

  <svg class="footer-band" viewBox="0 0 482 16" preserveAspectRatio="none" aria-hidden="true">
    <path d="M0 10.8 H482 V12.4 H0 Z" fill="var(--brand-blue)"/>
    <path d="M358 10.8 Q362 2 372 2 H482 V12.4 H358 Z" fill="var(--mid-blue)"/>
    <path d="M0 12.6 H482 V13.4 H0 Z" fill="var(--flap-blue)"/>
  </svg>
  <span class="footer-url">www.tavrin.ch</span>
</section>

<svg class="envelope-flap" viewBox="0 0 526 71" preserveAspectRatio="none" aria-hidden="true">
  <path d="M0 71 C2 50 8 44 30 40 L290 6 Q345 -3 395 6 L495 24 Q520 28 526 55 L526 71 Z" fill="var(--flap-blue)"/>
</svg>

<section class="envelope" aria-label="C5 envelope">
  <div class="brand"><span class="brand-square"></span><span class="brand-name">TaVrn</span></div>
  <svg class="footer-band" viewBox="0 0 526 16" preserveAspectRatio="none" aria-hidden="true">
    <path d="M0 10.8 H526 V12.4 H0 Z" fill="var(--brand-blue)"/>
    <path d="M388 10.8 Q392 2 402 2 H526 V12.4 H388 Z" fill="var(--mid-blue)"/>
    <path d="M0 12.6 H526 V13.4 H0 Z" fill="var(--flap-blue)"/>
  </svg>
  <span class="footer-url">www.tavrin.ch</span>
</section>

</body>
</html>
```